Vornel Wellness Business Card

A Double Sided Business Card

I am a private company in Melbourne, Australia, working in the Health industry. I am a nutritionist and lifestyle coach, whom specialises in using raw foods ie. fruits/nuts/vegetables to help heal my clients and enable them to achieve their ultimate state of health.

I want a sophisticated design and colour for my card that appeals to both men and women from teenage through to elderly.

Front of Card:

Red apple peel spiral in the shape of an apple. I would like a leaf/leaves coming off the stem of the apple. Please see attachments for example.

***On Right Hand side of Image is business Name: Vornel Wellness

Underneath LOGO use slogan " Let Food Be Your Medicine"

***Use Deep Red and Blues for Text Colouring

Back of Card:

Marisol Dekkert
Nutritional Specialist and Lifestyle Coach

Specialising in: Diseased Conditions
Weight Management
Achieving your Ultimate State of Health

enquiries@vornelwellness.com.au 0457 396 504

**Make sure the front design of the card flows onto the back.
Updates

Email address has been amended, Also more specific details have been given for apple peel Image, and another image attached as example of Leaf on stem of apple.

I little more insight into what sort of feel were trying to create. We're apart of the health industry, and we want the card to have a medical/clinical feeling about it.

Target Market(s)

Males and Females from teenages to elderly

Industry/Entity Type

Business

Requirements
Must have
• Red Apple Peel Spiral, in the shape of an apple, with a leaf/leaves attached to stem.
***Must be in the shape of an apple
***Please use coloring on inside of apple peel to resemble inside of an apple.
Nice to have
• I would like my card to have a clinical feel.
Should not have
• We don't want the image of the apple to look like a Christmas decoration

```html
<!DOCTYPE html>
<html lang="en">
<head>
<meta charset="utf-8">
<title>Vornel Wellness Business Card</title>
<link rel="stylesheet" href="https://fonts.googleapis.com/css2?family=Quicksand:wght@500;600;700&display=swap">
<style>
  :root {
    --navy: #141a45;
    --deep-red: #d0202a;
    --silver: #cfd1d6;
    --mist: #eceef1;
    --white: #ffffff;
    --ink: #2b2d33;
    --soft-text: #d9dbe3;
    --backdrop: #f3f1ec;
  }
  * { margin: 0; padding: 0; box-sizing: border-box; }
  html, body { width: 1200px; height: 900px; overflow: hidden; }
  body {
    background: var(--backdrop);
    font-family: "Quicksand", sans-serif;
    position: relative;
  }
  .card {
    position: absolute;
    width: 640px;
    height: 390px;
    overflow: hidden;
    box-shadow: 0 10px 24px rgba(0,0,0,0.22);
    background: var(--navy);
  }
  .card-back { left: 180px; top: 45px; }
  .card-front { left: 385px; top: 462px; }
  .card-art { position: absolute; inset: 0; }

  /* Back card: contact */
  .red-stripes { position: absolute; left: 18px; top: 0; display: flex; gap: 6px; }
  .red-stripes span { display: block; width: 10px; height: 150px; background: var(--deep-red); }
  .identity { position: absolute; left: 72px; top: 64px; }
  .person-name { color: var(--deep-red); font-size: 28px; font-weight: 500; line-height: 1.1; white-space: nowrap; }
  .person-role { color: var(--soft-text); font-size: 18px; font-weight: 500; line-height: 1.15; letter-spacing: 0.3px; white-space: nowrap; }
  .divider { position: absolute; left: 300px; top: 60px; width: 2px; height: 92px; background: var(--soft-text); }
  .contact { position: absolute; left: 316px; top: 80px; list-style: none; }
  .contact li { display: flex; align-items: center; gap: 8px; color: var(--white); font-size: 17px; font-weight: 500; margin-bottom: 12px; white-space: nowrap; }
  .contact li.phone { font-size: 20px; }
  .contact svg { width: 18px; height: 18px; flex: none; }
  .specialties { position: absolute; left: 68px; top: 216px; }
  .specialties h2 { color: var(--navy); font-size: 20px; font-weight: 600; margin-bottom: 8px; }
  .specialties ul { list-style: none; }
  .specialties li { color: var(--ink); font-size: 17px; font-weight: 500; line-height: 27px; }
  .specialties li::before { content: "· "; }

  /* Front card: brand */
  .brand-mark { position: absolute; left: 230px; top: 62px; width: 180px; height: 180px; border-radius: 50%; background: var(--deep-red); }
  .brand { position: absolute; left: 0; right: 0; top: 262px; text-align: center; }
  .brand-name { color: var(--navy); font-size: 38px; font-weight: 600; line-height: 1.1; }
  .brand-tagline { color: var(--ink); font-size: 19px; font-weight: 600; }
</style>
</head>
<body>

<section class="card card-back" aria-label="Business card back">
  <svg class="card-art" viewBox="0 0 640 390" preserveAspectRatio="none" aria-hidden="true">
    <defs>
      <linearGradient id="sweep-back" x1="0" y1="0" x2="1" y2="0">
        <stop offset="0" stop-color="#c9ccd2"/>
        <stop offset="0.55" stop-color="#f4f5f7"/>
        <stop offset="1" stop-color="#ffffff"/>
      </linearGradient>
    </defs>
    <rect width="640" height="390" fill="var(--navy)"/>
    <path d="M0 125 C120 190 300 230 640 285 L640 370 C420 395 200 340 0 320 Z" fill="url(#sweep-back)"/>
    <path d="M0 260 C160 270 360 300 640 330 L640 372 C430 392 200 345 0 322 Z" fill="#ffffff"/>
    <path d="M0 322 C160 335 300 370 400 390 L0 390 Z" fill="var(--navy)"/>
    <path d="M640 372 C560 380 480 385 420 390 L640 390 Z" fill="#dfe1e6"/>
  </svg>
  <div class="red-stripes"><span></span><span></span><span></span></div>
  <div class="identity">
    <h1 class="person-name">Marisol Dekkert</h1>
    <p class="person-role">Nutritional Specialist</p>
    <p class="person-role">Lifestyle Coach</p>
  </div>
  <div class="divider"></div>
  <ul class="contact">
    <li>
      <svg viewBox="0 0 24 24" fill="none" stroke="var(--deep-red)" stroke-width="1.8"><circle cx="12" cy="12" r="10"/><ellipse cx="12" cy="12" rx="4.5" ry="10"/><path d="M2 12h20M4 7h16M4 17h16"/></svg>
      enquiries@vornelwellness.com.au
    </li>
    <li class="phone">
      <svg viewBox="0 0 24 24" fill="var(--deep-red)"><path d="M6.6 2.5l3 3.2-1.9 2.6c1.2 2.6 3.3 4.8 6 6l2.6-1.9 3.2 3-1.8 3.6C10.5 18.6 5.4 13.5 3 6.3z"/></svg>
      0457 396 504
    </li>
  </ul>
  <div class="specialties">
    <h2>Specialising in:</h2>
    <ul>
      <li>Diseased Conditions</li>
      <li>Weight Management</li>
      <li>Achieving your Ultimate State of Health</li>
    </ul>
  </div>
</section>

<section class="card card-front" aria-label="Business card front">
  <svg class="card-art" viewBox="0 0 640 390" preserveAspectRatio="none" aria-hidden="true">
    <defs>
      <linearGradient id="sweep-front" x1="0" y1="0" x2="1" y2="0">
        <stop offset="0" stop-color="#ffffff"/>
        <stop offset="0.6" stop-color="#e4e6ea"/>
        <stop offset="1" stop-color="#c4c7cd"/>
      </linearGradient>
    </defs>
    <rect width="640" height="390" fill="var(--navy)"/>
    <path d="M0 300 C200 230 420 150 640 115 L640 315 C420 300 200 320 0 330 Z" fill="url(#sweep-front)"/>
    <path d="M0 300 C200 255 420 245 640 255 L640 330 C420 345 200 355 0 345 Z" fill="#ffffff"/>
    <path d="M0 345 C120 355 230 372 300 390 L0 390 Z" fill="var(--navy)"/>
    <path d="M640 330 C560 345 500 370 470 390 L640 390 Z" fill="var(--navy)"/>
    <path d="M300 390 C360 372 420 360 470 390 Z" fill="#d6d8dd"/>
  </svg>
  <div class="brand-mark" aria-hidden="true"></div>
  <div class="brand">
    <p class="brand-name">Vornel Wellness</p>
    <p class="brand-tagline">Let Food Be Your Medicine</p>
  </div>
</section>

</body>
</html>
```